BLS Business Card 2018

Larkmere Chiropractic. We have two locations that we want to advertise on the same card. Brightvale OrthoCore campus address: 3815 Pellham Dr., Suite 240, Cedar Hollow, ST 39417. Northgate address: 246 Willowmere Dr., Building D., Northgate, ST 39284. website: www.drlarkmere-example.com. o:(555)555-0147 f:(555)555-0183

Target Market(s)

Health care decision makers: primary care doctors and mothers

Contact Information for Business Card

I have no idea; up for any suggestions and I'd do much better picking from examples versus describing what I'm looking for. We are in a very high end location and would like the cards to look really sharp.

Requirements
Must have
• My name, Martin R Belvane, D.C.

```html
<!DOCTYPE html>
<html lang="en">
<head>
<meta charset="utf-8">
<title>Larkmere Chiropractic – Business Card</title>
<link rel="stylesheet" href="https://fonts.googleapis.com/css2?family=Cinzel:wght@500;600&family=Roboto+Condensed:wght@400;700&display=swap">
<style>
  :root {
    --canvas: #e7e5e1;
    --card-dark: #1d1d1f;
    --card-dark-2: #29292b;
    --panel-grey-top: #737373;
    --panel-grey-bottom: #4d4d4f;
    --divider: #b9b9b9;
    --ink-light: #f2f2f2;
    --ink-soft: #d6d6d6;
    --figure-tone: rgba(255,255,255,0.07);
  }
  * { box-sizing: border-box; margin: 0; padding: 0; }
  html, body { width: 1200px; height: 911px; overflow: hidden; }
  body {
    background: var(--canvas);
    position: relative;
    font-family: "Roboto Condensed", Arial, sans-serif;
  }
  .card {
    position: absolute;
    left: 290px;
    width: 620px;
    height: 354px;
    border-radius: 10px;
    overflow: hidden;
    box-shadow: 0 10px 28px rgba(0,0,0,0.22);
  }
  .card--back { top: 58px; background: var(--card-dark); }
  .card--front { top: 478px; background: linear-gradient(160deg, var(--card-dark-2), var(--card-dark)); }

  /* back side */
  .back-brand { position: absolute; left: 0; top: 0; width: 345px; height: 100%; }
  .wordmark {
    font-family: "Cinzel", Georgia, serif;
    font-weight: 500;
    color: var(--ink-light);
    line-height: 1;
  }
  .back-brand .wordmark { position: absolute; left: 118px; top: 134px; }
  .back-brand .wordmark__main { font-size: 36px; letter-spacing: 1px; display: block; }
  .back-brand .wordmark__sub { font-size: 20px; letter-spacing: 1px; display: block; margin-top: 6px; }
  .brand-mark {
    position: absolute; left: 78px; top: 140px;
    width: 30px; height: 30px; border-radius: 50%;
    border: 1.5px solid var(--ink-soft);
  }
  .figure-art {
    position: absolute; right: 6px; bottom: 8px; width: 120px; height: 110px;
    background: radial-gradient(ellipse at center, rgba(255,255,255,0.08), rgba(255,255,255,0) 70%);
  }
  .contact-panel {
    position: absolute; right: 0; top: 0; width: 275px; height: 100%;
    background: linear-gradient(180deg, var(--panel-grey-top), var(--panel-grey-bottom));
    border-left: 2px solid var(--divider);
    padding: 30px 22px 0 28px;
    color: var(--ink-light);
  }
  .contact-panel__name {
    font-weight: 700; font-size: 19px; letter-spacing: 0.3px;
    text-transform: uppercase; margin-bottom: 22px; white-space: nowrap;
  }
  .contact-panel p { font-size: 13.5px; line-height: 1.38; color: var(--ink-soft); }
  .contact-panel .address { margin-bottom: 6px; }
  .contact-list { list-style: none; margin-top: 8px; }
  .contact-list li {
    display: flex; align-items: center; gap: 8px;
    font-size: 13.5px; line-height: 1.55; color: var(--ink-soft);
  }
  .contact-list svg { width: 12px; height: 12px; flex: none; fill: var(--ink-light); }

  /* front side */
  .front-figure {
    position: absolute; left: 150px; top: 40px; width: 330px; height: 280px;
    border-radius: 50%;
    background: radial-gradient(ellipse at center, var(--figure-tone), rgba(255,255,255,0) 70%);
  }
  .card--front .wordmark { position: absolute; left: 0; right: 0; top: 106px; text-align: center; font-weight: 600; }
  .card--front .wordmark__main { font-size: 64px; letter-spacing: 2px; display: block; }
  .card--front .wordmark__sub { font-size: 36px; letter-spacing: 2px; display: block; margin-top: 4px; }
  .front-url {
    position: absolute; left: 0; right: 0; top: 238px; text-align: center;
    font-size: 13px; letter-spacing: 6px; color: var(--ink-soft); text-transform: uppercase;
  }
</style>
</head>
<body>

<section class="card card--back" aria-label="Business card, back">
  <div class="back-brand">
    <span class="brand-mark"></span>
    <div class="wordmark">
      <span class="wordmark__main">LARKMERE</span>
      <span class="wordmark__sub">CHIROPRACTIC</span>
    </div>
    <div class="figure-art" role="img" aria-label="Line illustration of a stretching human figure"></div>
  </div>
  <div class="contact-panel">
    <h1 class="contact-panel__name">Martin R Belvane, D.C.</h1>
    <p class="address">Brightvale OrthoCore campus :<br>3815 Pellham Dr., Suite 240<br>Cedar Hollow, ST 39417</p>
    <p class="address">Northgate address:<br>246 Willowmere Dr., Building D.<br>Northgate, ST 39284.</p>
    <ul class="contact-list">
      <li><svg viewBox="0 0 24 24"><path d="M6.6 10.8a15.1 15.1 0 0 0 6.6 6.6l2.2-2.2a1 1 0 0 1 1-.25 11.4 11.4 0 0 0 3.6.57 1 1 0 0 1 1 1V20a1 1 0 0 1-1 1A17 17 0 0 1 3 4a1 1 0 0 1 1-1h3.5a1 1 0 0 1 1 1c0 1.25.2 2.45.57 3.57a1 1 0 0 1-.25 1z"/></svg>(555)555-0147</li>
      <li><svg viewBox="0 0 24 24"><path d="M6 3h10v5H6zM4 9h16a2 2 0 0 1 2 2v6h-4v4H6v-4H2v-6a2 2 0 0 1 2-2zm4 7v3h8v-3z"/></svg>(555)555-0183</li>
      <li><svg viewBox="0 0 24 24"><circle cx="12" cy="12" r="10"/></svg>www.drlarkmere-example.com</li>
    </ul>
  </div>
</section>

<section class="card card--front" aria-label="Business card, front">
  <div class="front-figure" role="img" aria-label="Faint large illustration of a stretching human figure"></div>
  <div class="wordmark">
    <span class="wordmark__main">LARKMERE</span>
    <span class="wordmark__sub">CHIROPRACTIC</span>
  </div>
  <div class="front-url">www.drlarkmere-example.com</div>
</section>

</body>
</html>
```